Website for "Bright Morrow Ltd" cleaning bsuiness

We require a website to expose our business to the local market. We want to provide background on who we are and what we do but in an easily digestible way. We clean domestic and commercial premises and want to provide a list of all of our services to potential customers. We operate out of Warrington in the UK.

We would like the website to be animated in some way so that the experience of using it is not dull or mundane. This website needs to be an extension of our company.

Target Market(s)

30 - 60 year olds for Domestic plus commercial clients

Industry/Entity Type

Cleaning Service

Coding

Coded - Design and coding required

Number of Pages Required

4 page

Font styles to use
Sans Serif

Colors
0455a3
3176b5
85acd3
cfdeed
ffffff
000000
1b1b1b
c8c8c8
757575

Requirements
Must have
• Logo which has been provided. Theme based around the logo and its colours. Simple layout to avoid confusion.
Nice to have
• Animations where possible to impress the customer.
Should not have
• any pictures of cleaning equipment, fairies, maids etc

```html
<!DOCTYPE html>
<html lang="en">
<head>
<meta charset="utf-8">
<title>Bright Morrow Ltd – Professional Cleaning Services</title>
<link href="https://fonts.googleapis.com/css2?family=Jost:wght@400;500&family=Open+Sans:ital,wght@0,400;0,600;0,700;1,400&display=swap" rel="stylesheet">
<style>
:root{
  --blue:#0455a3;
  --blue-mid:#3176b5;
  --blue-soft:#85acd3;
  --blue-pale:#cfdeed;
  --white:#ffffff;
  --black:#000000;
  --ink:#1b1b1b;
  --line:#c8c8c8;
  --grey:#757575;
  --band:#1b5aa6;
  --card:#3a78c0;
  --slate:#3b4656;
  --footer:#1d2330;
  --green:#3aa53a;
  --head:"Jost",sans-serif;
  --body:"Open Sans",sans-serif;
}
*{box-sizing:border-box;margin:0;padding:0}
html,body{width:1200px;height:2571px;overflow:hidden}
body{position:relative;background:var(--white);font-family:var(--body);color:var(--ink)}
.abs{position:absolute}
a{color:inherit;text-decoration:none}
p{font-size:12.5px;line-height:1.72;color:var(--grey)}
.read-more{font-size:12.5px;font-weight:700;color:var(--blue)}
.section-title{position:absolute;left:0;width:1200px;text-align:center;font-family:var(--head);font-weight:400;font-size:29px}
@keyframes rise{from{opacity:0;transform:translateY(14px)}to{opacity:1;transform:none}}

/* top bar */
.topbar{left:672px;top:0;width:528px;height:34px;background:var(--blue);display:flex;align-items:center;color:var(--white)}
.social-top{display:flex;height:34px}
.social-top span{width:34px;height:34px;border-right:1px solid rgba(255,255,255,.35);display:flex;align-items:center;justify-content:center}
.social-top span:first-child{border-left:1px solid rgba(255,255,255,.35)}
.social-top span i{width:11px;height:11px;border-radius:50%;background:var(--white);display:block}
.call{margin-left:24px;display:flex;align-items:center;gap:9px;font-size:15px}
.call b{font-weight:700}

/* nav */
.nav{left:0;top:34px;width:1200px;height:72px;background:var(--white)}
.menu{position:absolute;left:320px;top:0;height:72px;display:flex;align-items:center;gap:24px;font-size:14.5px;color:var(--ink)}
.menu .active{color:var(--blue-mid)}
.estimate{position:absolute;left:964px;top:15px;width:137px;height:40px;background:var(--green);color:var(--white);font-weight:700;font-size:14px;display:flex;align-items:center;justify-content:center;border-radius:2px}
.brand-disc{left:86px;top:0;width:206px;height:206px;border-radius:50%;background:var(--white);z-index:3;display:flex;align-items:center;justify-content:center;text-align:center;box-shadow:0 2px 6px rgba(0,0,0,.12)}
.brand-disc span{font-family:var(--head);font-weight:500;font-size:30px;line-height:1.05;color:var(--blue)}

/* hero */
.hero{left:0;top:106px;width:1200px;height:425px;background:linear-gradient(180deg,#e7e6e3 0%,#c9c2b6 45%,#8e8376 75%,#b9afa2 100%)}
.hero-title{left:0;top:232px;width:1200px;text-align:center;font-family:var(--head);font-size:70px;color:var(--white);text-shadow:0 2px 8px rgba(0,0,0,.45);animation:rise 1s ease both}
.hero-sub{left:0;top:306px;width:1200px;text-align:center;font-family:var(--head);font-size:30px;color:var(--white);text-shadow:0 2px 6px rgba(0,0,0,.45)}
.search{left:315px;top:362px;width:569px;height:42px;display:flex}
.search .field{flex:0 0 374px;background:var(--white);font-size:13px;color:var(--grey);display:flex;align-items:center;padding-left:18px}
.search .go{flex:1;background:var(--blue);color:var(--white);font-weight:700;font-size:15px;display:flex;align-items:center;justify-content:center}
.hero-dots{left:534px;top:483px;display:flex;gap:6px}
.hero-dots i{width:29px;height:5px;background:var(--white);display:block}
.hero-dots i:first-child{background:var(--blue)}

/* welcome */
.welcome-title{left:98px;top:570px;font-family:var(--head);font-size:27px}
.welcome-text{left:98px;top:617px;width:720px}
.welcome-more{left:98px;top:731px}
.seal{left:833px;top:549px}

/* what we do */
.what{left:0;top:806px;width:1200px;height:425px;background:var(--band)}
.what .section-title{top:36px;color:var(--white)}
.feature{position:absolute;width:462px;height:108px}
.feature .panel{position:absolute;left:60px;top:0;right:0;bottom:0;background:var(--card);padding:14px 16px 0 74px}
.feature h3{font-family:var(--head);font-weight:400;font-size:23px;color:var(--white);margin-bottom:6px}
.feature p{color:var(--white);font-size:12px;line-height:1.6}
.feature .badge{position:absolute;left:0;top:-6px;width:120px;height:120px;border-radius:50%;background:var(--white);border:5px solid var(--blue-soft);display:flex;align-items:center;justify-content:center}

/* services */
.services .section-title{top:1264px;color:var(--ink)}
.svc{position:absolute;top:1320px;width:243px}
.svc .photo{height:171px;border:4px solid #eee;box-shadow:0 0 0 1px var(--line)}
.svc h3{font-family:var(--head);font-weight:400;font-size:19px;margin:16px 0 6px;white-space:nowrap}
.svc p{font-size:12px;line-height:1.7}
.svc .read-more{display:block;margin-top:12px}
.arrow{position:absolute;top:1387px;width:38px;height:38px;border-radius:50%;background:#8d8d8d;display:flex;align-items:center;justify-content:center}

/* who we are */
.who{left:0;top:1663px;width:1200px;height:372px;background:linear-gradient(90deg,#2c3543,#4b5666 60%,#3a4453)}
.who-photo{left:99px;top:1707px;width:367px;height:281px;border:4px solid var(--white);background:linear-gradient(180deg,#cfe3f2 0%,#b7c4cf 35%,#8a969e 55%,#5e9a3d 72%,#4f8a2f 100%)}
.who-title{left:511px;top:1700px;font-family:var(--head);font-size:27px;color:var(--white)}
.who-text{left:511px;top:1745px;width:580px}
.who-text p{color:#e3e7ec;font-size:12px;line-height:1.75;margin-bottom:12px}
.who-more{left:511px;top:1975px;color:var(--white)}

/* testimonials */
.testi .section-title{top:2066px;color:var(--ink)}
.quote-disc{left:106px;top:2118px;width:120px;height:120px;border-radius:50%;background:#ececec}
.avatar{left:196px;top:2116px;width:90px;height:112px;border-radius:50%;background:linear-gradient(180deg,#c9d4df,#5f6f82);border:3px solid var(--white)}
.testi-text{left:319px;top:2122px;width:775px;font-style:italic;font-size:12.5px}
.testi-name{left:316px;top:2206px;font-weight:600;font-size:15px;color:var(--blue);letter-spacing:.5px}
.testi-dots{left:580px;top:2218px;display:flex;gap:5px}
.testi-dots i{width:9px;height:9px;border-radius:50%;background:#a5a5a5;display:block}
.testi-dots i:first-child{background:var(--blue)}

/* footer */
.footer{left:0;top:2276px;width:1200px;height:295px;background:var(--footer);border-top:5px solid var(--blue)}
.foot-brand{left:103px;top:2335px;width:250px;font-family:var(--head);font-weight:500;font-size:38px;line-height:1.08;color:var(--white)}
.foot-col h4{font-family:var(--head);font-weight:400;font-size:20px;color:var(--white);margin-bottom:14px}
.foot-col{position:absolute;top:2310px;color:#d7dbe2;font-size:12px}
.foot-col ul{list-style:none;line-height:20.6px}
.foot-col p{color:#d7dbe2;font-size:12px;line-height:1.65}
.email-field{width:230px;height:33px;background:var(--white);color:var(--grey);font-size:12px;display:flex;align-items:center;padding-left:12px;margin-top:12px}
.subscribe{width:100px;height:34px;border:2px solid var(--white);color:var(--white);font-weight:700;font-size:12px;display:flex;align-items:center;justify-content:center;margin-top:14px;border-radius:2px}
.contact-row{display:flex;gap:18px;align-items:flex-start;margin-bottom:14px;line-height:1.5}
.contact-row svg{flex:0 0 14px;margin-top:2px}
.foot-rule{left:0;top:2518px;width:1200px;height:1px;background:rgba(255,255,255,.12)}
.copyright{left:98px;top:2535px;font-size:12px;color:#c3c8d0}
.foot-social{left:951px;top:2526px;display:flex;gap:8px}
.foot-social i{width:33px;height:33px;border:2px solid var(--white);border-radius:50%;display:block}
</style>
</head>
<body>

<div class="abs topbar">
  <div class="social-top"><span><i></i></span><span><i></i></span><span><i></i></span><span><i></i></span></div>
  <div class="call">
    <svg width="18" height="18" viewBox="0 0 24 24" fill="none" stroke="#fff" stroke-width="1.6"><circle cx="12" cy="12" r="10.5"/><path d="M8.5 7.5l2 2-1 1.5c.8 1.6 2 2.8 3.5 3.5l1.5-1 2 2-1.3 1.3c-3.8-.4-7.6-4.2-8-8z" fill="#fff" stroke="none"/></svg>
    <span>Call Us On : <b>01925 555 014</b></span>
  </div>
</div>

<header class="abs nav">
  <nav class="menu">
    <a class="active">Home</a><a>About</a><a>Who We Are</a><a>What We do</a><a>Our Services</a><a>Blog</a><a>Contact</a>
    <svg width="15" height="15" viewBox="0 0 16 16" fill="none" stroke="#1b1b1b" stroke-width="2"><circle cx="6.5" cy="6.5" r="4.8"/><path d="M10 10l4.5 4.5"/></svg>
  </nav>
  <a class="estimate">FREE ESTIMATE</a>
</header>
<div class="abs brand-disc"><span>Bright<br>Morrow Ltd</span></div>

<section class="abs hero" role="img" aria-label="Photo of a bright, clean kitchen with granite worktops and white cabinets"></section>
<h1 class="abs hero-title">Bright Morrow Ltd</h1>
<div class="abs hero-sub">Professional Cleaning Services</div>
<form class="abs search"><div class="field">Enter zip/Postal Code</div><div class="go">FIND MY LOCATION</div></form>
<div class="abs hero-dots"><i></i><i></i><i></i><i></i></div>

<h2 class="abs welcome-title">Welcome to Bright Morrow Ltd</h2>
<p class="abs welcome-text">Bright Morrow is a local cleaning team serving homes and businesses across Warrington. We bring reliable people, careful methods and friendly service to every visit, whether it is a weekly tidy, a deep clean or a one-off job. Our staff are trained, insured and proud of the results they leave behind, and we always plan around you.</p>
<a class="abs read-more welcome-more">READ MORE &gt;&gt;</a>
<svg class="abs seal" width="298" height="222" viewBox="0 0 298 222" aria-hidden="true">
  <circle cx="149" cy="100" r="96" fill="#d6dbe0"/>
  <circle cx="149" cy="100" r="80" fill="var(--blue-mid)"/>
  <circle cx="149" cy="100" r="60" fill="var(--blue)"/>
</svg>

<section class="abs what">
  <h2 class="section-title">What We Do</h2>
  <div class="feature" style="left:103px;top:111px">
    <div class="panel"><h3>Quality Cleaning</h3><p>Trained teams who take real care with every room and surface.</p></div>
    <div class="badge"><svg width="46" height="46" viewBox="0 0 24 24" fill="#1b1b1b"><path d="M12 2l2.9 6 6.6.9-4.8 4.6 1.2 6.5L12 16.9 6.1 20l1.2-6.5L2.5 8.9 9.1 8z"/></svg></div>
  </div>
  <div class="feature" style="left:638px;top:111px">
    <div class="panel"><h3>Professional Services</h3><p>Insured, vetted staff who arrive on time and work to a plan.</p></div>
    <div class="badge"><svg width="44" height="44" viewBox="0 0 24 24" fill="none" stroke="#1b1b1b" stroke-width="2"><rect x="3" y="7" width="18" height="13" rx="2"/><path d="M9 7V4h6v3M3 13h18"/></svg></div>
  </div>
  <div class="feature" style="left:103px;top:257px">
    <div class="panel"><h3>Affordable Rates</h3><p>Clear, fair prices with no hidden extras on any booking we take.</p></div>
    <div class="badge"><svg width="46" height="46" viewBox="0 0 24 24" fill="#1b1b1b"><path d="M3 3h9l9 9-9 9-9-9z"/><circle cx="7.5" cy="7.5" r="1.8" fill="#fff"/></svg></div>
  </div>
  <div class="feature" style="left:638px;top:257px">
    <div class="panel"><h3>Customized Services</h3><p>Plans shaped around your home, your office and your timetable.</p></div>
    <div class="badge"><svg width="46" height="46" viewBox="0 0 24 24" fill="none" stroke="#1b1b1b" stroke-width="2.4"><circle cx="12" cy="12" r="4"/><path d="M12 2v4M12 18v4M2 12h4M18 12h4M4.9 4.9l2.8 2.8M16.3 16.3l2.8 2.8M4.9 19.1l2.8-2.8M16.3 7.7l2.8-2.8"/></svg></div>
  </div>
</section>

<section class="services">
  <h2 class="section-title">Our Services</h2>
  <article class="svc" style="left:98px"><div class="photo" role="img" aria-label="Photo of a tidy living room with a grey sofa" style="background:linear-gradient(180deg,#8a7f93,#6d6670 55%,#c9c3bb)"></div><h3>Domestic Cleaning</h3><p>Regular or one-off home cleans planned around your busy week.</p><a class="read-more">READ MORE &gt;&gt;</a></article>
  <article class="svc" style="left:351px"><div class="photo" role="img" aria-label="Photo of a bright open-plan office lobby" style="background:linear-gradient(180deg,#f1f3f5,#d8dde2 55%,#b9c0c6)"></div><h3>Commercial Cleaning</h3><p>Offices, shops and premises kept spotless before and after hours.</p><a class="read-more">READ MORE &gt;&gt;</a></article>
  <article class="svc" style="left:603px"><div class="photo" role="img" aria-label="Photo of a house with autumn trees and a green lawn" style="background:linear-gradient(180deg,#b96a3a,#8c7a62 45%,#5f7d4a)"></div><h3>Green Cleaning</h3><p>Gentle, eco friendly products that are kind to family and pets.</p><a class="read-more">READ MORE &gt;&gt;</a></article>
  <article class="svc" style="left:857px"><div class="photo" role="img" aria-label="Photo of moving boxes in an empty room" style="background:linear-gradient(180deg,#cfd0c2,#b99a76 60%,#9a7350)"></div><h3>Move In/Move Out Cleaning</h3><p>A full top to bottom clean so every move starts fresh and easy.</p><a class="read-more">READ MORE &gt;&gt;</a></article>
  <div class="arrow" style="left:74px"><svg width="12" height="14" viewBox="0 0 12 14" fill="none" stroke="#fff" stroke-width="2.2"><path d="M8 2L3 7l5 5"/></svg></div>
  <div class="arrow" style="left:1088px"><svg width="12" height="14" viewBox="0 0 12 14" fill="none" stroke="#fff" stroke-width="2.2"><path d="M4 2l5 5-5 5"/></svg></div>
</section>

<section class="abs who" role="img" aria-label="Dim blurred interior backdrop"></section>
<div class="abs who-photo" role="img" aria-label="Photo of a large family house with a porch and green lawn"></div>
<h2 class="abs who-title">Who We Are</h2>
<div class="abs who-text">
  <p>We are a family-run cleaning company based in Warrington, serving local homes and businesses with care, honesty and attention to detail on every visit.</p>
  <p>Since we started, our aim has been simple: to give people back their time and a space they are proud of. Our cleaners are local, fully trained and supported by a small office team who answer every call. We listen to what you need, agree a clear plan and keep the same friendly faces on your job wherever we can. From busy family homes to shops, offices and rental properties, we adapt our work to suit you and check the results before we leave.</p>
</div>
<a class="abs read-more who-more">READ MORE &gt;&gt;</a>

<section class="testi">
  <h2 class="section-title">Customer Testimonials</h2>
  <div class="abs quote-disc"></div>
  <div class="abs avatar" role="img" aria-label="Portrait photo of the customer"></div>
  <p class="abs testi-text">The team at Bright Morrow have cleaned our home every fortnight for two years now. They are always on time, polite and thorough, and the house feels brand new after every visit. I would happily recommend them to anyone looking for a cleaner they can trust with their keys.</p>
  <div class="abs testi-name">DANIEL HARPER</div>
  <div class="abs testi-dots"><i></i><i></i><i></i></div>
</section>

<footer class="abs footer"></footer>
<div class="abs foot-brand">Bright<br>Morrow Ltd</div>
<div class="foot-col" style="left:441px">
  <h4>Information</h4>
  <ul><li>Home</li><li>About</li><li>Who We Are</li><li>What We do</li><li>Our Services</li><li>Blog</li><li>Contact</li></ul>
</div>
<div class="foot-col" style="left:617px">
  <h4>Newsletter</h4>
  <p>Register your email address to get<br>information about us</p>
  <div class="email-field">Email Address</div>
  <div class="subscribe">SUBSCRIBE</div>
</div>
<div class="foot-col" style="left:917px">
  <h4>Contact Us</h4>
  <div class="contact-row"><svg width="14" height="16" viewBox="0 0 14 18" fill="#fff"><path d="M7 0a7 7 0 0 0-7 7c0 5 7 11 7 11s7-6 7-11a7 7 0 0 0-7-7zm0 9.5A2.5 2.5 0 1 1 7 4.5a2.5 2.5 0 0 1 0 5z"/></svg><span>12 Sankey Street,<br>Warrington, WA1 1XX</span></div>
  <div class="contact-row"><svg width="14" height="14" viewBox="0 0 24 24" fill="#fff"><path d="M6 2l4 4-2 3c1.5 3 4 5.5 7 7l3-2 4 4-3 3C10 20 4 14 3 5z"/></svg><span>01925 555 014</span></div>
  <div class="contact-row"><svg width="14" height="14" viewBox="0 0 24 24" fill="#fff"><rect x="2" y="7" width="20" height="14" rx="2"/><rect x="6" y="2" width="12" height="6" fill="none" stroke="#fff" stroke-width="2"/></svg><span>01925 555 027</span></div>
  <div class="contact-row"><svg width="14" height="12" viewBox="0 0 24 18" fill="#fff"><path d="M0 0h24v18H0z"/><path d="M0 0l12 9 12-9" fill="none" stroke="#1d2330" stroke-width="2"/></svg><span>hello@brightmorrow.co.uk</span></div>
</div>
<div class="abs foot-rule"></div>
<div class="abs copyright">Copyrights © 2016, Bright Morrow Ltd. All rights reserved.</div>
<div class="abs foot-social"><i></i><i></i><i></i><i></i></div>

</body>
</html>
```